Transport & Storage Company needs a revamp of current card

Would like to keep same colours & basic design but would like to "sharpen" up look of card.

Please remove "The Brisk Haulers"

Please add 1800 418 239 on front & back of card

Please add email address on back of card - colin@bluegatefreight.com.au

I would like our ABN No - 38 214 906 731 on back of card (which currently has logo only). Logo on back of card can be removed if insufficient space.

Please design another card (same as above) but with Maren Ashcombe - 0431 702 548, maren@bluegatefreight.com.au

I do not want cards to look "too busy" so please re-arrange layout of card if necessary.

Target Market(s)

Transport & Storage

Industry/Entity Type

It Company

Contact Information for Business Card

Please refer to attached current business card

Font styles to use
Other font styles liked:
• Tahoma

Requirements
Must have
• Refer to project decsription
Nice to have
Should not have

```html
<!DOCTYPE html>
<html lang="en">
<head>
<meta charset="utf-8">
<title>Bluegate Freight – Business Card</title>
<link rel="stylesheet" href="https://fonts.googleapis.com/css2?family=Open+Sans:wght@400;600;700&display=swap">
<style>
  :root {
    --backdrop: #adab85;
    --brand-purple: #763a84;
    --stripe-grey: #58585a;
    --card-white: #ffffff;
    --text-light: #ffffff;
  }
  * { box-sizing: border-box; margin: 0; padding: 0; }
  html, body {
    width: 1083px;
    height: 1200px;
    overflow: hidden;
    background: var(--backdrop);
    font-family: "Open Sans", Tahoma, sans-serif;
  }
  .card {
    position: absolute;
    overflow: hidden;
    background: var(--card-white);
    box-shadow: 0 2px 8px rgba(0, 0, 0, 0.25);
  }
  .card-front { left: 76px; top: 47px; width: 923px; height: 540px; }
  .card-back  { left: 76px; top: 623px; width: 926px; height: 541px; background: var(--brand-purple); }
  .card-shapes { position: absolute; inset: 0; width: 100%; height: 100%; }

  .brand-name {
    position: absolute;
    color: var(--brand-purple);
    font-weight: 700;
    line-height: 1;
    white-space: nowrap;
    letter-spacing: -0.3px;
    text-align: center;
  }
  .card-front .brand-name { left: 510px; top: 132px; width: 370px; font-size: 42px; }

  .contact {
    position: absolute;
    color: var(--text-light);
    line-height: 1;
    white-space: nowrap;
  }
  .person-name { left: 46px; top: 290px; font-size: 38px; font-weight: 600; }
  .mobile      { left: 46px; top: 369px; font-size: 31px; letter-spacing: 1.5px; }
  .office      { left: 46px; top: 411px; font-size: 31px; letter-spacing: 1.5px; }
  .website     { left: 46px; top: 467px; font-size: 31px; letter-spacing: 0.8px; }

  .logo-band {
    position: absolute;
    left: 0; top: 51px;
    width: 100%; height: 174px;
    background: var(--card-white);
  }
  .card-back .brand-name { left: 0; top: 114px; width: 100%; font-size: 48px; }

  .back-detail { left: 0; width: 100%; text-align: center; }
  .abn        { top: 299px; font-size: 19px; }
  .back-phone { top: 348px; font-size: 32px; letter-spacing: 1px; }
  .back-email { top: 396px; font-size: 32px; }
</style>
</head>
<body>

  <section class="card card-front" aria-label="Business card front">
    <svg class="card-shapes" viewBox="0 0 1077 630" preserveAspectRatio="none" aria-hidden="true">
      <polygon points="0,42 1041,630 0,630" fill="var(--brand-purple)"/>
      <polygon points="0,0 129,0 1077,618 1077,630 1052,630 0,15" fill="var(--stripe-grey)"/>
    </svg>
    <div class="brand-name">Bluegate Freight</div>
    <p class="contact person-name">Colin Trevethan</p>
    <p class="contact mobile">0452 387 160</p>
    <p class="contact office">1800 418 239</p>
    <p class="contact website">www.bluegatefreight.com.au</p>
  </section>

  <section class="card card-back" aria-label="Business card back">
    <div class="logo-band"></div>
    <div class="brand-name">Bluegate Freight</div>
    <p class="contact back-detail abn">ABN No - 38 214 906 731</p>
    <p class="contact back-detail back-phone">1800 418 239</p>
    <p class="contact back-detail back-email">colin@bluegatefreight.com.au</p>
  </section>

</body>
</html>
```